Website Header Development

I am after a redesign of the Header of a website www.tlvoltaris.com.au.
This project is for the header only, and should fit in with the rest of the site
Target Market(s)
Business
Requirements
Should not have
- Over the top. Keep it simple

```html
<!DOCTYPE html>
<html lang="en">
<head>
<meta charset="utf-8">
<title>Voltaris Energy – Resource Efficiency</title>
<link rel="stylesheet" href="https://fonts.googleapis.com/css2?family=Alegreya:wght@700&family=Alegreya+Sans:wght@400;500;700&display=swap">
<style>
  :root {
    --navy: #1f2f86;
    --heading-navy: #0f1778;
    --band-blue: #2540a0;
    --nav-green: #1f7f3a;
    --nav-green-dark: #1a7034;
    --text: #222222;
    --muted: #9a9a9a;
    --border: #c9c9c9;
    --white: #ffffff;
    --page-bg: #f6f6f6;
    --photo-a: #e9eef2;
    --photo-b: #c8cfd6;
  }
  * { box-sizing: border-box; margin: 0; padding: 0; }
  html, body { width: 1200px; height: 556px; overflow: hidden; }
  body { position: relative; background: var(--page-bg); font-family: "Alegreya Sans", sans-serif; color: var(--text); }

  .page { position: absolute; left: 48px; top: 0; width: 1117px; height: 556px; background: var(--white); overflow: hidden; }

  .site-header { position: absolute; left: 0; top: 0; width: 1117px; height: 123px; }
  .header-band { position: absolute; left: 0; top: 0; }

  .brand { position: absolute; left: 64px; top: 52px; display: flex; align-items: center; gap: 12px; }
  .brand-name { font-weight: 700; font-size: 36px; color: var(--navy); letter-spacing: -0.3px; line-height: 1; }
  .brand-dot { width: 22px; height: 22px; border-radius: 50%; background: var(--navy); }

  .contact { position: absolute; left: 892px; top: 16px; color: var(--white); font-size: 19px; }
  .contact-line { display: flex; align-items: center; gap: 8px; height: 30px; }
  .contact-icon { width: 23px; height: 23px; border: 2px solid var(--white); border-radius: 50%; display: flex; align-items: center; justify-content: center; font-size: 14px; font-weight: 700; }

  .main-nav { position: absolute; left: 0; top: 128px; width: 1117px; height: 59px; background: var(--nav-green); overflow: hidden; }
  .main-nav::after { content: ""; position: absolute; left: 990px; top: 0; width: 70px; height: 59px; background: var(--nav-green-dark); transform: skewX(40deg); }
  .nav-item { position: absolute; top: 0; height: 59px; line-height: 59px; color: var(--white); font-size: 13.5px; text-decoration: none; white-space: nowrap; }
  .nav-item.is-strong { font-size: 16px; font-weight: 700; top: 6px; }

  .page-title { position: absolute; left: 113px; top: 222px; font-family: "Alegreya", serif; font-weight: 700; font-size: 25px; color: var(--heading-navy); letter-spacing: 0.3px; white-space: nowrap; }

  .intro { position: absolute; left: 67px; top: 276px; width: 208px; font-size: 16px; line-height: 28px; }
  .intro p { margin-bottom: 29px; }

  .hero-photo { position: absolute; left: 322px; top: 290px; width: 391px; height: 261px; background: linear-gradient(110deg, var(--photo-a) 0%, var(--photo-b) 100%); }

  .sidebar { position: absolute; left: 823px; top: 189px; width: 210px; }
  .search { width: 205px; height: 33px; border: 1px solid var(--border); display: flex; align-items: center; gap: 8px; padding-left: 8px; color: var(--muted); font-size: 15px; }
  .newsletter-title { margin-top: 40px; font-family: "Alegreya", serif; font-weight: 700; font-size: 22px; line-height: 33px; letter-spacing: 1.6px; color: var(--navy); }
  .newsletter-text { margin-top: 20px; width: 205px; font-size: 11.5px; font-weight: 700; line-height: 28px; color: var(--text); }
  .newsletter-text.is-follow { margin-top: 0; white-space: nowrap; }
  .field { width: 206px; height: 29px; border: 1px solid var(--border); background: var(--white); margin: 6px 0 8px; }
</style>
</head>
<body>
  <div class="page">
    <header class="site-header">
      <svg class="header-band" width="1117" height="123" viewBox="0 0 1117 123" aria-hidden="true">
        <rect x="0" y="0" width="1117" height="6" fill="var(--band-blue)"/>
        <path d="M560 0 L1117 0 L1117 123 L676 123 C640 110 640 60 610 30 C595 12 580 4 560 0 Z" fill="var(--band-blue)"/>
      </svg>
      <div class="brand">
        <span class="brand-name">voltaris energy</span>
        <span class="brand-dot"></span>
      </div>
      <div class="contact">
        <div class="contact-line"><span class="contact-icon">P</span>+61 ( 02) 4817 3920</div>
        <div class="contact-line"><span class="contact-icon">E</span>info@tlvoltaris.com.au</div>
      </div>
    </header>

    <nav class="main-nav">
      <a class="nav-item is-strong" style="left:94px" href="#">Home</a>
      <a class="nav-item" style="left:178px" href="#">About Us</a>
      <a class="nav-item" style="left:267px" href="#">Services</a>
      <a class="nav-item" style="left:347px" href="#">Projects and Case Studies</a>
      <a class="nav-item is-strong" style="left:531px" href="#">Financial Information</a>
      <a class="nav-item" style="left:727px" href="#">News</a>
      <a class="nav-item" style="left:793px" href="#">Contact</a>
    </nav>

    <h1 class="page-title">Resource Efficiency – Sustainable Solutions</h1>

    <div class="intro">
      <p>Is your business performing as well as your competitors?</p>
      <p>Are your fixed costs comparable to industry leaders?</p>
      <p>Is your business becoming less profitable with increased energy, waste and water prices?</p>
    </div>

    <div class="hero-photo" role="img" aria-label="Photo of a businessman holding up a jigsaw puzzle piece labelled Solution"></div>

    <aside class="sidebar">
      <div class="search">
        <svg width="16" height="16" viewBox="0 0 16 16" aria-hidden="true"><circle cx="9.5" cy="6.5" r="5" fill="none" stroke="var(--muted)" stroke-width="2"/><line x1="6" y1="10" x2="1.5" y2="14.5" stroke="var(--muted)" stroke-width="2.5" stroke-linecap="round"/></svg>
        Search
      </div>
      <h2 class="newsletter-title">Voltaris<br>Energy<br>Newsletter</h2>
      <p class="newsletter-text">Would you like to receive our regular monthly Newsletter? Please fill in your Name:</p>
      <div class="field"></div>
      <p class="newsletter-text is-follow">Let us know your email address so we</p>
    </aside>
  </div>
</body>
</html>
```